Business Card Design

We need a business card designed for our new company. Prefer a black card with white logo & writing.

Contact Information for Business Card

Ted Galloway, address: 7-4812 Fernhollow Road, Abbotsford, BC, V3K 8R2, Office Phone: 604-712-3390, Cell: 604-947-2164, Email: ted@resinworkshub.ca

Colors

Designer to choose only greyscale colors for use in the design.

```html
<!DOCTYPE html>
<html lang="en">
<head>
<meta charset="utf-8">
<title>Resin Works Hub – Business Card</title>
<link rel="stylesheet" href="https://fonts.googleapis.com/css2?family=Poppins:wght@300;400;700&display=swap">
<style>
  :root{
    --backdrop:#1f1f21;
    --card:#232326;
    --ink:#ffffff;
    --ink-soft:#e9e9e9;
    --emboss:#3a3a3e;
    --accent-bar:#f1f0ea;
  }
  *{margin:0;padding:0;box-sizing:border-box}
  html,body{width:1200px;height:711px;overflow:hidden;background:var(--backdrop)}
  body{position:relative;font-family:"Poppins",sans-serif;color:var(--ink)}
  .card{position:absolute;width:500px;height:286px;background:var(--card);border-radius:4px;box-shadow:0 12px 30px rgba(0,0,0,.55);overflow:hidden}
  .card--front{left:70px;top:90px}
  .card--back{left:630px;top:330px}

  /* front */
  .front-mark{position:absolute;inset:0;display:flex;align-items:center;justify-content:center;gap:12px}
  .front-mark__square{width:22px;height:22px;background:var(--emboss)}
  .front-mark__name{font-weight:700;font-size:30px;letter-spacing:1px;color:var(--emboss);text-transform:uppercase}

  /* back */
  .brand{position:absolute;left:34px;top:40px;display:flex;align-items:center;gap:9px}
  .brand__square{width:14px;height:14px;background:var(--ink)}
  .brand__name{font-weight:700;font-size:20px;letter-spacing:.5px;text-transform:uppercase;color:var(--ink)}

  .identity{position:absolute;right:64px;top:30px;text-align:right}
  .identity__name{font-size:24px;line-height:1.1;font-weight:300}
  .identity__first{font-weight:700}
  .identity__role{font-size:10.5px;font-weight:400;color:var(--ink-soft);margin-top:2px}
  .identity-bar{position:absolute;right:34px;top:24px;width:16px;height:56px;background:var(--accent-bar)}

  .address{position:absolute;right:34px;top:150px;text-align:right;font-size:11px;font-weight:300;line-height:1.55;color:var(--ink-soft)}

  .contact{position:absolute;left:34px;bottom:26px;list-style:none;font-size:11.5px;font-weight:300;line-height:1}
  .contact__item{display:flex;align-items:center;gap:10px;margin-top:6px}
  .contact__icon{width:11px;height:11px;flex:none;fill:none;stroke:var(--ink);stroke-width:1.4}
</style>
</head>
<body>
  <section class="card card--front" aria-label="Card front">
    <div class="front-mark">
      <span class="front-mark__square"></span>
      <span class="front-mark__name">Resin Works Hub</span>
    </div>
  </section>

  <section class="card card--back" aria-label="Card back">
    <div class="brand">
      <span class="brand__square"></span>
      <span class="brand__name">Resin Works Hub</span>
    </div>

    <span class="identity-bar"></span>
    <div class="identity">
      <p class="identity__name"><span class="identity__first">Ted</span> Galloway</p>
      <p class="identity__role">Founder &amp; CEO</p>
    </div>

    <p class="address">7-4812 Fernhollow Road,<br>Abbotsford, BC, V3K 8R2.</p>

    <ul class="contact">
      <li class="contact__item">
        <svg class="contact__icon" viewBox="0 0 12 12"><path d="M2 1.5l2 .3.8 2.2-1.2.9a6 6 0 0 0 3.5 3.5l.9-1.2 2.2.8.3 2A1 1 0 0 1 9.5 11 8.5 8.5 0 0 1 1 2.5a1 1 0 0 1 1-1z"/></svg>
        <span>604-712-3390</span>
      </li>
      <li class="contact__item">
        <svg class="contact__icon" viewBox="0 0 12 12"><rect x="3" y="1" width="6" height="10" rx="1"/><line x1="5.3" y1="9" x2="6.7" y2="9"/></svg>
        <span>604-947-2164</span>
      </li>
      <li class="contact__item">
        <svg class="contact__icon" viewBox="0 0 12 12"><circle cx="6" cy="6" r="5"/><ellipse cx="6" cy="6" rx="2.2" ry="5"/><line x1="1" y1="6" x2="11" y2="6"/></svg>
        <span>www.resinworkshub.ca</span>
      </li>
      <li class="contact__item">
        <svg class="contact__icon" viewBox="0 0 12 12"><rect x="1" y="2.5" width="10" height="7" rx=".6"/><path d="M1 3l5 3.6L11 3"/></svg>
        <span>ted@resinworkshub.ca</span>
      </li>
    </ul>
  </section>
</body>
</html>
```